Zielgruppe
Verkauf und Einbau von Fenstern, Haustüren, Rollläden, Raffstore, Markisen, Insektenschutzgitter, Plissees
Aufgabenstellung
Es soll das gleiche Farbschema meines Firmenlogos haben. Grauer Hintergrund, kleine gelbe Akzente und schwarze Schrift

```html
<!DOCTYPE html>
<html lang="de">
<head>
<meta charset="utf-8">
<title>Rahmenwerk – Fenster, Haustüren, Sonnenschutz</title>
<link href="https://fonts.googleapis.com/css2?family=Baumans&family=Open+Sans:wght@400;600;700&display=swap" rel="stylesheet">
<style>
:root{
  --yellow:#fcc40f;
  --black:#111;
  --text:#1d1d1d;
  --light:#efefef;
  --mid:#7b7b7b;
  --band:#8c8c8c;
  --white:#fff;
}
*{margin:0;padding:0;box-sizing:border-box}
html,body{width:1200px;height:3725px;overflow:hidden;background:var(--white)}
body{position:relative;font-family:'Open Sans',sans-serif;color:var(--text)}
.abs{position:absolute}
.photo{position:absolute}
/* header */
.brand{left:50px;top:14px;width:160px;text-align:center}
.brand-mark{width:40px;height:40px;border:4px solid var(--yellow);border-radius:50%;margin:0 auto 8px}
.brand-name{font-family:'Baumans',sans-serif;color:var(--yellow);font-size:22px;line-height:1}
.brand-sub{font-size:7px;letter-spacing:.3px;color:var(--text);margin-top:3px}
.nav a{position:absolute;top:52px;font-family:'Baumans',sans-serif;font-size:21px;color:var(--text);text-decoration:none;padding:3px 8px;border-radius:3px}
.nav a.active{background:var(--yellow)}
/* hero */
.hero-title{left:90px;top:198px;width:560px;font-family:'Baumans',sans-serif;font-weight:400;font-size:48px;line-height:44px;color:var(--yellow);white-space:nowrap}
.hero-sub{left:92px;top:362px;width:520px;font-family:'Baumans',sans-serif;font-size:21px;line-height:21px;white-space:nowrap}
.btn{position:absolute;display:flex;align-items:center;justify-content:center;font-weight:700;font-size:15px;color:var(--black)}
.btn-fill{background:var(--yellow)}
.btn-line{border:3px solid var(--yellow);background:var(--white)}
/* who */
.who-panel{left:561px;top:659px;width:636px;height:459px;background:var(--light)}
.who-title{left:577px;top:700px;font-family:'Baumans',sans-serif;font-weight:400;font-size:31px}
.who-lead{left:577px;top:776px;font-size:19px}
.who-text{left:577px;top:829px;width:540px;font-size:17px;line-height:21px;font-weight:600;letter-spacing:.4px}
.btn-dark{left:574px;top:1006px;width:224px;height:61px;border:3px solid var(--black);border-radius:8px;font-size:15px}
/* offer */
.section-title{left:0;width:1200px;text-align:center;font-family:'Baumans',sans-serif;font-weight:400;font-size:31px}
.offer-text{left:60px;top:1226px;width:1080px;text-align:center;font-family:'Baumans',sans-serif;font-size:20px;line-height:20px;color:#444}
.feature{left:93px;top:1310px;width:1016px;height:252px;border-radius:10px;overflow:hidden}
.feature-info{position:absolute;left:0;top:0;width:509px;height:100%;background:var(--mid)}
.feature-info h3{position:absolute;left:17px;top:110px;font-family:'Baumans',sans-serif;font-weight:400;font-size:26px;color:var(--yellow)}
.feature-info p{position:absolute;left:17px;top:162px;width:400px;font-family:'Baumans',sans-serif;font-size:20px;line-height:20px;color:var(--white)}
.tile{position:absolute;width:322px;height:253px;border-radius:8px;overflow:hidden}
.tile span{position:absolute;left:0;bottom:0;width:100%;height:68px;background:rgba(90,90,90,.75);display:flex;align-items:center;justify-content:center;font-family:'Baumans',sans-serif;font-size:27px;color:var(--yellow)}
/* news */
.news{left:0;top:2202px;width:1200px;height:707px;background:var(--light)}
.news-text{left:84px;top:2298px;width:1060px;font-family:'Baumans',sans-serif;font-size:21px;line-height:20px;white-space:nowrap}
.filter{position:absolute;height:66px;border:3px solid var(--yellow);border-radius:9px;display:flex;align-items:center;justify-content:center;font-family:'Baumans',sans-serif;font-size:21px;background:var(--light)}
.filter.on{background:var(--yellow)}
.slide{position:absolute;top:2577px;height:253px;border-radius:8px;overflow:hidden}
.dot{position:absolute;top:2855px;width:16px;height:16px;border-radius:50%;background:#9a9a9a}
.dot.on{background:var(--yellow)}
/* contact */
.contact-band{left:0;top:2996px;width:1200px;height:388px;background:var(--band)}
.contact-photo{left:123px;top:2909px;width:354px;height:475px;background:linear-gradient(160deg,#9a9a9a,#6f7a7e)}
.contact-title{left:625px;top:3034px;font-family:'Baumans',sans-serif;font-weight:400;font-size:31px;color:var(--black)}
.contact-sub{left:629px;top:3103px;width:550px;font-family:'Baumans',sans-serif;font-size:21px;line-height:20px;color:var(--white)}
.contact-text{left:629px;top:3168px;width:550px;font-size:17px;line-height:21px;color:var(--white)}
/* footer */
.footer{left:0;top:3411px;width:1200px;height:262px;background:var(--black)}
.footer-brand{left:85px;top:3460px;width:200px;text-align:center}
.footer-brand .brand-mark{width:56px;height:56px;margin-bottom:14px}
.footer-brand .brand-name{font-size:25px}
.footer-brand .brand-sub{color:var(--white);font-size:8px}
.fcol h4{font-family:'Baumans',sans-serif;font-weight:400;font-size:21px;color:var(--white);margin-bottom:10px}
.fcol li{list-style:none;font-family:'Baumans',sans-serif;font-size:13px;color:var(--white);line-height:26px}
.fcol li::before{content:"• "}
.contact-line{position:absolute;left:837px;display:flex;align-items:center;gap:14px;font-size:12px;color:var(--white)}
.copyright{left:0;top:3692px;width:1200px;text-align:center;font-size:17px;color:#333}
</style>
</head>
<body>

<header>
  <div class="abs brand"><div class="brand-mark"></div><div class="brand-name">RAHMENWERK</div><div class="brand-sub">FENSTER HAUSTÜREN SONNENSCHUTZ</div></div>
  <nav class="nav">
    <a class="active" style="left:415px">Start</a>
    <a style="left:508px">Aktuelles</a>
    <a style="left:643px">Wer Sin Wir</a>
    <a style="left:810px">Unser Angebot</a>
    <a style="left:1000px">Kontakt</a>
  </nav>
</header>

<section class="hero">
  <h1 class="abs hero-title">Perfekte Lösungen Für<br>Ihr Zuhause - Qualität,<br>Die Begeistert</h1>
  <p class="abs hero-sub">Entdecken Sie Unsere Hochwertigen Fenster,<br>Türen, Rollläden Und Mehr</p>
  <div class="btn btn-fill" style="left:93px;top:480px;width:193px;height:56px">Jetzt Entdecken</div>
  <div class="btn btn-line" style="left:330px;top:480px;width:192px;height:56px">Angebot Anfordern</div>
  <div class="photo" role="img" aria-label="Auswahl an Fenstern und Türen in Holz, Weiß und Anthrazit" style="left:619px;top:217px;width:531px;height:296px;background:linear-gradient(90deg,#4a4a4a,#e9e9ee 30%,#c9a77e 55%,#5a5d62 80%,#fff)"></div>
</section>

<section class="who">
  <div class="photo" role="img" aria-label="Handwerker montiert ein weißes Fenster" style="left:0;top:659px;width:538px;height:459px;background:linear-gradient(100deg,#cfcfcf,#e8b43a 45%,#f2f2f2)"></div>
  <div class="abs who-panel"></div>
  <h2 class="abs who-title">Wer Sind Wir</h2>
  <p class="abs who-lead">Ihr vertrauenswürdiger Partner für Fenster und Türen</p>
  <p class="abs who-text">Mit jahrelanger Erfahrung und einem Engagement für Exzellenz liefern wir maßgeschneiderte Lösungen, die Ihr Zuhause schöner und sicherer machen. Unser Expertenteam sorgt dafür, dass jede Installation perfekt ausgeführt wird</p>
  <div class="btn btn-dark">Mehr Über Uns Erfahren</div>
</section>

<section class="offer">
  <h2 class="abs section-title" style="top:1140px">Unser Angebot</h2>
  <p class="abs offer-text">Wir bieten eine breite Palette von Produkten an, die auf Ihre Bedürfnisse zugeschnitten sind, einschließlich:<br>Fenster, Haustüren, Rollläden, Außenjalousien, Markisen, Insektenschutz und Plisseejalousien.</p>
  <div class="abs feature">
    <div class="feature-info"><h3>Verkauf Und Einbau Von Fenstern</h3><p>Hochwertige Fenster für Stil und Energieeffizienz. Präzise Installation für langanhaltende Leistung</p></div>
    <div class="photo" role="img" aria-label="Monteur dichtet einen Fensterrahmen ab" style="left:509px;top:0;width:507px;height:252px;background:linear-gradient(100deg,#f3f3f3,#e6e6e6 40%,#eab236 75%,#d9d9d9)"></div>
  </div>
  <div class="tile" role="img" aria-label="Moderne Haustür" style="left:88px;top:1605px;background:linear-gradient(#f2f2f2,#8a8a85)"><span>Haustüren</span></div>
  <div class="tile" role="img" aria-label="Rollläden vor einem Fenster" style="left:437px;top:1605px;background:linear-gradient(#2c2c2c,#6d7a6a 50%,#2a2a2a)"><span>Rollläden</span></div>
  <div class="tile" role="img" aria-label="Raffstore an einem modernen Gebäude" style="left:785px;top:1605px;background:linear-gradient(#f1f1f1,#3a3d46 45%,#7a8c6a)"><span>Raffstore</span></div>
  <div class="tile" role="img" aria-label="Markisen an einer Ladenfront" style="left:82px;top:1903px;background:linear-gradient(#e8dcc7,#5a4b3c 50%,#8a2a22)"><span>Markisen</span></div>
  <div class="tile" role="img" aria-label="Insektenschutzgitter" style="left:432px;top:1903px;background:linear-gradient(#efe9e3,#d8cfc8)"><span>Insektenschutzgitter</span></div>
  <div class="tile" role="img" aria-label="Plissee an einem Dachfenster" style="left:781px;top:1903px;background:linear-gradient(135deg,#9a9a9a,#5e5e5e 50%,#eeeeee)"><span>Plissees</span></div>
</section>

<section>
  <div class="abs news"></div>
  <h2 class="abs section-title" style="top:2230px">Aktuelles</h2>
  <p class="abs news-text">Werfen Sie Einen Blick Auf Einige Unserer Erfolgreichen Projekte Und Überzeugen Sie Sich Von Der Qualität<br>Unserer Arbeit.</p>
  <div class="filter on" style="left:84px;top:2363px;width:225px">Fenstern</div>
  <div class="filter" style="left:340px;top:2363px;width:224px">Haustüren</div>
  <div class="filter" style="left:596px;top:2363px;width:224px">Rollläden</div>
  <div class="filter" style="left:852px;top:2363px;width:224px">Raffstore</div>
  <div class="filter" style="left:184px;top:2460px;width:225px">Markisen</div>
  <div class="filter" style="left:463px;top:2460px;width:248px">Insektenschutzgitter</div>
  <div class="filter" style="left:766px;top:2460px;width:225px">Plissees</div>
  <div class="slide" role="img" aria-label="Innenraum mit Holzmöbeln" style="left:0;width:59px;background:linear-gradient(#dcd7cf,#c99a5b)"></div>
  <div class="slide" role="img" aria-label="Wintergarten mit dunklen Fensterrahmen" style="left:84px;width:322px;background:linear-gradient(#e4e4e4,#2e3a32 50%,#d8d8d8)"></div>
  <div class="slide" role="img" aria-label="Helles Wohnzimmer mit großen Fenstern" style="left:429px;width:323px;background:linear-gradient(#f2f2f2,#d7d3cc)"></div>
  <div class="slide" role="img" aria-label="Dunkles Holzhaus mit Panoramafenster" style="left:776px;width:323px;background:linear-gradient(#d9e2e6,#3a3a3a 40%,#6f7f5a)"></div>
  <div class="slide" role="img" aria-label="Fensterfront in einem Wohnraum" style="left:1122px;width:78px;background:linear-gradient(#ececec,#c2a170)">
    <svg style="position:absolute;left:6px;top:112px" width="34" height="24" viewBox="0 0 34 24"><path d="M2 12H30M21 3l9 9-9 9" fill="none" stroke="#fff" stroke-width="2.5"/></svg>
  </div>
  <div class="dot" style="left:517px"></div><div class="dot" style="left:548px"></div><div class="dot on" style="left:580px"></div><div class="dot" style="left:609px"></div><div class="dot" style="left:640px"></div><div class="dot" style="left:670px"></div>
</section>

<section>
  <div class="abs contact-band"></div>
  <div class="photo contact-photo" role="img" aria-label="Foto: Berater des Kundenservice am Telefon"></div>
  <h2 class="abs contact-title">Kontaktieren Sie Uns</h2>
  <p class="abs contact-sub">Wir Sind Hier, Um Ihre Fragen Zu Beantworten Und Ihnen Zu Helfen</p>
  <p class="abs contact-text">Haben Sie Fragen Oder Benötigen Sie Eine Beratung? Unser Freundliches Team Steht Ihnen Jederzeit Zur Verfügung. Zögern Sie Nicht, Uns Zu Kontaktieren Und Den Nächsten Schritt Zu Einem Schöneren Zuhause Zu Machen</p>
  <div class="btn btn-fill" style="left:629px;top:3287px;width:275px;height:55px;border-radius:3px">Jetzt Kontakt Aufnehmen</div>
</section>

<footer>
  <div class="abs footer"></div>
  <div class="abs brand footer-brand"><div class="brand-mark"></div><div class="brand-name">RAHMENWERK</div><div class="brand-sub">FENSTER HAUSTÜREN SONNENSCHUTZ</div></div>
  <div class="abs fcol" style="left:399px;top:3432px"><h4>Navigation</h4><ul><li>Start</li><li>Wer Sin Wier</li><li>Aktuelles</li><li>Unsere Angebot</li><li>Kontakt</li></ul></div>
  <div class="abs fcol" style="left:602px;top:3430px"><h4>Leistungen</h4><ul><li>Fenstern</li><li>Haustüren</li><li>Rollläden</li><li>Raffstore</li><li>Markisen</li><li>Insektenschutzgitter</li><li>Plissees</li></ul></div>
  <div class="abs fcol" style="left:837px;top:3436px"><h4>Kontakt</h4></div>
  <div class="contact-line" style="top:3476px"><svg width="16" height="12" viewBox="0 0 16 12"><rect x="0.5" y="0.5" width="15" height="11" rx="1" fill="#fcc40f"/><path d="M1 1l7 6 7-6" fill="none" stroke="#111" stroke-width="1.2"/></svg>kontakt@rahmenwerk-beispiel.de</div>
  <div class="contact-line" style="top:3522px"><svg width="16" height="16" viewBox="0 0 24 24"><path d="M6.6 10.8a15 15 0 006.6 6.6l2.2-2.2a1 1 0 011-.25 11 11 0 003.5.56 1 1 0 011 1V20a1 1 0 01-1 1A17 17 0 013 4a1 1 0 011-1h3.5a1 1 0 011 1 11 11 0 00.56 3.5 1 1 0 01-.25 1z" fill="#fcc40f"/></svg>+(49)30 5550192</div>
  <div class="contact-line" style="top:3568px"><svg width="16" height="18" viewBox="0 0 24 28"><path d="M12 0a9 9 0 00-9 9c0 7 9 17 9 17s9-10 9-17a9 9 0 00-9-9zm0 12.5A3.5 3.5 0 1112 5.5a3.5 3.5 0 010 7z" fill="#fcc40f"/></svg>Halle, Saxony Lindenweg 8,</div>
  <p class="abs copyright">Copyright 2024 By Rahmenwerk Gmbh</p>
</footer>

</body>
</html>
```